The design should look similar to the uploaded example to accommodate the information needed for a business card template. I would like to see the colors orange and charcoal grey incorporated along with the logo.The following should be on the back of the card SPECIALIZING IN NEW AND USED TIRES & WHEELS FOR:- Loaders- Skid Steers- Telehandlers- Boom Lifts- Forklifs and moreELIMINATING DOWNTIMEWheel Exchange Program for New & Used Foam Filled and Solid Rubber TiresSPECIALTY SERVICES- Foam Filling Tires- Largest Tire Press in SE- ONSITE Forklift Tire Press- Boom Truck Services - Rubber Tracks

Target Market(s)

New and Existing Customers

Industry/Entity Type

Business

Contact Information for Business Card

NAMEHEAVY DUTY TIRE, LLC8470 Belvedere RoadWest Palm Beach, FL 33411P: 844-HD-TIRESF: 561-431-6469C:E: W: WWW.GRANITERIMSUPPLY-EXAMPLE.COM

Font styles to use
Sans Serif

Colors
f37122
333333

Requirements
Must have
• The logo and the information indicated for the backside of the card
Nice to have
• Keep the orange and charcoal grey colors

```html
<!DOCTYPE html>
<html lang="en">
<head>
<meta charset="utf-8">
<title>Granite Rim Supply, LLC — Business Card</title>
<link rel="stylesheet" href="https://fonts.googleapis.com/css2?family=Arimo:wght@400;700&family=Roboto+Slab:wght@700&display=swap">
<style>
  :root {
    --orange: #f99e52;
    --charcoal: #354444;
    --charcoal-dark: #2e3838;
    --white: #ffffff;
    --ink: #111111;
    --backdrop: #e4e4e4;
    --badge-grey: #d6d9d9;
  }
  * { box-sizing: border-box; margin: 0; padding: 0; }
  html, body { width: 1189px; height: 1200px; overflow: hidden; }
  body { background: var(--backdrop); font-family: "Arimo", Arial, sans-serif; position: relative; }

  .card {
    position: absolute; left: 136px; width: 918px; height: 522px;
    overflow: hidden; background: var(--white);
    box-shadow: 0 4px 14px rgba(0,0,0,0.25);
  }
  .card--front { top: 46px; }
  .card--back { top: 624px; }

  /* Front */
  .front-band { position: absolute; left: 0; right: 0; top: 0; height: 215px; background: var(--orange); }
  .front-stripe { position: absolute; left: 0; right: 0; top: 219px; height: 16px; background: var(--charcoal); }
  .front-footer { position: absolute; left: 0; right: 0; top: 434px; bottom: 0; background: var(--charcoal); }
  .company-name {
    position: absolute; right: 25px; top: 84px;
    font-family: "Roboto Slab", Georgia, serif; font-weight: 700;
    font-size: 45px; color: var(--white); letter-spacing: 0.5px; white-space: nowrap;
  }
  .brand-mark {
    position: absolute; left: 28px; top: 138px; width: 350px; height: 350px;
    border-radius: 50%; background: var(--charcoal-dark);
    display: flex; flex-direction: column; align-items: center; justify-content: center;
    font-family: "Arimo", Arial, sans-serif; font-weight: 700;
    color: var(--orange); font-size: 54px; line-height: 1.1; text-align: center;
  }
  .contact-list { position: absolute; right: 34px; top: 241px; list-style: none; }
  .contact-list li {
    display: flex; justify-content: flex-end; align-items: center;
    height: 37px; font-size: 24px; color: var(--ink); white-space: nowrap;
  }
  .contact-list svg { width: 20px; height: 20px; margin-left: 20px; flex: none; }
  .address {
    position: absolute; right: 25px; top: 466px;
    font-size: 24px; color: var(--white); white-space: nowrap;
  }

  /* Back */
  .back-panel { position: absolute; left: 0; right: 0; top: 0; height: 363px; background: var(--charcoal); }
  .back-glow {
    position: absolute; left: 600px; top: -30px; width: 360px; height: 360px;
    border-radius: 50%; background: rgba(249,158,82,0.12);
  }
  .services-title {
    position: absolute; left: 47px; top: 40px;
    font-size: 34px; font-weight: 400; color: var(--white); letter-spacing: 0.5px; white-space: nowrap;
  }
  .services-list { position: absolute; left: 47px; top: 108px; list-style: none; }
  .services-list li {
    display: flex; align-items: center; height: 42px;
    font-size: 25px; color: var(--white); white-space: nowrap;
  }
  .services-list li::before {
    content: ""; width: 10px; height: 10px; border: 4px solid var(--white);
    border-radius: 50%; margin: 0 26px 0 2px; flex: none;
  }
  .specialties { position: absolute; left: 520px; top: 40px; width: 370px; color: var(--white); }
  .specialties h3 {
    font-size: 16px; font-weight: 700; color: var(--orange); line-height: 1.3; letter-spacing: 0.3px;
  }
  .machine-list {
    list-style: none; margin: 10px 0 18px; display: grid;
    grid-template-columns: 1fr 1fr; row-gap: 6px; column-gap: 10px;
  }
  .machine-list li { font-size: 18px; white-space: nowrap; }
  .machine-list li::before { content: "– "; color: var(--orange); }
  .specialties p { font-size: 17px; line-height: 1.35; margin-top: 8px; }

  .back-footer { position: absolute; left: 0; right: 0; top: 363px; bottom: 0; background: var(--white); }
  .footer-mark {
    position: absolute; left: 59px; top: 376px; width: 134px; height: 134px;
    border-radius: 50%; background: var(--charcoal-dark);
    display: flex; flex-direction: column; align-items: center; justify-content: center;
    font-family: "Arimo", Arial, sans-serif; font-weight: 700;
    font-size: 20px; line-height: 1.15; color: var(--orange); text-align: center;
  }
  .partner-badge { position: absolute; background: var(--badge-grey); border-radius: 10px; }
  .partner-badge--rental { left: 389px; top: 388px; width: 140px; height: 108px; }
  .partner-badge--retread { left: 721px; top: 388px; width: 140px; height: 108px; }
</style>
</head>
<body>

<section class="card card--front" aria-label="Business card front">
  <div class="front-band"></div>
  <div class="front-stripe"></div>
  <div class="front-footer"></div>
  <h1 class="company-name">GRANITE RIM SUPPLY LLC</h1>
  <div class="brand-mark"><span>GRANITE</span><span>RIM</span></div>
  <ul class="contact-list">
    <li>844-GR-WHEEL
      <svg viewBox="0 0 20 20"><rect x="1" y="1" width="18" height="18" fill="#111"/><path d="M4 8c0-3 12-3 12 0v1h-3V8H7v1H4z M6 10h8l1 6H5z" fill="#fff"/></svg></li>
    <li>027361940582
      <svg viewBox="0 0 20 20"><rect x="1" y="1" width="18" height="18" fill="#111"/><rect x="6" y="3" width="8" height="14" rx="1" fill="#fff"/><rect x="7.5" y="5" width="5" height="4" fill="#111"/></svg></li>
    <li>561-278-9053
      <svg viewBox="0 0 20 20"><rect x="1" y="1" width="18" height="18" fill="#111"/><rect x="6" y="3" width="8" height="5" fill="#fff"/><rect x="4" y="8" width="12" height="6" fill="#fff"/><rect x="6" y="12" width="8" height="5" fill="#fff" stroke="#111"/></svg></li>
    <li>info@graniterimsupply-example.com
      <svg viewBox="0 0 20 20"><rect x="1" y="1" width="18" height="18" fill="#111"/><rect x="4" y="5.5" width="12" height="9" fill="#fff"/><path d="M4 5.5l6 5 6-5" fill="none" stroke="#111" stroke-width="1.2"/></svg></li>
    <li>www.graniterimsupply-example.com
      <svg viewBox="0 0 20 20"><rect x="1" y="1" width="18" height="18" fill="#111"/><circle cx="10" cy="10" r="6.5" fill="#fff"/><path d="M7 6c2 1 1 3 3 3s1 3 3 4" fill="none" stroke="#111" stroke-width="1.5"/></svg></li>
  </ul>
  <p class="address">5126 Marston Lane, West Palm Beach, FL 33411</p>
</section>

<section class="card card--back" aria-label="Business card back">
  <div class="back-panel"></div>
  <div class="back-glow" aria-hidden="true"></div>
  <h2 class="services-title">SPECIALTY SERVICES</h2>
  <ul class="services-list">
    <li>Rubber Tracks</li>
    <li>Foam Filling Tires</li>
    <li>Boom Truck Services</li>
    <li>Largest Tire Press in SE</li>
    <li>ONSITE Forklift Tire Press</li>
  </ul>
  <div class="specialties">
    <h3>SPECIALIZING IN NEW AND USED<br>TIRES &amp; WHEELS FOR:</h3>
    <ul class="machine-list">
      <li>Loaders</li>
      <li>Skid Steers</li>
      <li>Telehandlers</li>
      <li>Boom Lifts</li>
      <li>Forklifts and more</li>
    </ul>
    <h3>ELIMINATING DOWNTIME</h3>
    <p>Wheel Exchange Program for New &amp; Used Foam Filled and Solid Rubber Tires</p>
  </div>
  <div class="back-footer"></div>
  <div class="footer-mark"><span>GRANITE</span><span>RIM</span></div>
  <div class="partner-badge partner-badge--rental" role="img" aria-label="Rental association membership badge"></div>
  <div class="partner-badge partner-badge--retread" role="img" aria-label="Retread association membership badge"></div>
</section>

</body>
</html>
```